Business software developers new website

We need to redesign our website. Our current website is http://www.plovencast.example/index.html, which is outdated and needs a new look. We moved out from web design and have concentrated more on the back end of the systems, for example, system support and security and cloud-based applications. Our major clients include both private and government sectors. We would like to see some designs that are all in one page, simple and clean. Prefer illustrator or obstructed images instead of real-life photos. Must look futuristic yet friendly. Attached the new logo for your references and good luck.

Target Market(s)

Medium to big company for their IT or data management. Either improve or upgrade their current system.

Industry/Entity Type

Business Software

Number of Pages Required

1 page

Colors

Designer to choose colors to be used in the design.

Requirements
Must have
• Simple and clean. Individual assets must be provided in the correct size and format(png or jpeg). Prefer Goggle fonts. Even though the logo color is red, grey and black, still prefer some modern colors that go well with red. When design, must consider the possibility to convert it into responsive.
Nice to have
• White background
Should not have
• real life photos, no slider

```html
<!DOCTYPE html>
<html lang="en">
<head>
<meta charset="utf-8">
<title>Plovencast.net — Business Software, Support, Security and Cloud</title>
<link href="https://fonts.googleapis.com/css2?family=Titillium+Web:wght@300;400;600&display=swap" rel="stylesheet">
<style>
:root{
  --red:#e21b36;
  --ink:#2b2b2b;
  --text:#555;
  --muted:#7a7a7a;
  --band:#f6f6f7;
  --pill:#ebebeb;
  --violet:#6a2ea2;
  --indigo:#4d52c8;
  --blue:#3f6ad8;
  --magenta:#d12f9e;
  --pink:#ef3f78;
  --footer:#343434;
  --line:#d9d9d9;
}
*{box-sizing:border-box;margin:0;padding:0}
html,body{width:1200px;height:3567px;overflow:hidden;background:#fff}
body{font-family:"Titillium Web",sans-serif;color:var(--text);position:relative}
.abs{position:absolute}
.center{left:0;width:1200px;text-align:center}

/* header */
.logo{left:144px;top:22px;font-size:34px;font-weight:400;color:var(--ink);letter-spacing:-0.5px;display:flex;align-items:center;gap:8px}
.logo .mark{width:14px;height:14px;background:var(--red);border-radius:50%}
.nav{top:30px;right:144px;display:flex;gap:31px;font-size:14.5px;color:#444}
.nav a{color:inherit;text-decoration:none}
.nav a.active{color:var(--red)}

/* hero */
.hero-text{left:144px;top:202px;width:350px;font-size:20.5px;line-height:33.5px;color:var(--ink);font-weight:400}
.hero-text em{font-style:normal;color:var(--red)}
.pill{left:144px;width:199px;height:43px;background:var(--pill);border-radius:22px;display:flex;align-items:center;font-size:15.5px;font-weight:600;color:var(--ink)}
.pill .ico{width:42px;height:43px;display:flex;align-items:center;justify-content:center;border-right:1px solid #d4d4d4;margin-right:12px}
.hero-art{left:543px;top:86px;width:657px;height:527px;border-radius:264px 0 0 264px;background:linear-gradient(135deg,#3e72d8 0%,#5650c6 55%,#7a35a8 100%)}

/* headings and copy */
h2{font-size:41px;font-weight:600;color:var(--red);line-height:1}
.lead{left:150px;width:900px;font-size:15.5px;line-height:25.5px;text-align:center;color:#555}
.btn{display:flex;align-items:center;justify-content:center;width:96px;height:35px;border-radius:18px;font-size:11.5px;text-transform:uppercase;color:#fff;background:linear-gradient(90deg,var(--violet),var(--indigo));letter-spacing:.2px}
.btn.soft{background:#e6e6e6;color:#555}

/* feature cards */
.card{width:300px;text-align:center}
.card .tile{width:94px;height:94px;border-radius:22px;margin:0 auto;display:flex;align-items:center;justify-content:center}
.card h3{font-size:18.5px;font-weight:600;margin-top:12px;line-height:1.2}
.card p{font-size:11px;line-height:18px;color:var(--muted);margin:10px auto 0;width:290px;height:54px}
.card .btn{margin:14px auto 0}

/* portfolio */
.shot{top:2054px;width:296px;height:343px;border:1px solid #ddd}

/* faq */
.q{font-size:20px;font-weight:400;color:var(--ink)}
.a{left:150px;width:900px;font-size:11.5px;line-height:19px;text-align:center;color:#666}
.rule{left:144px;width:911px;height:1px;background:var(--line)}

/* contact */
.field{top:3193px;width:218px;height:39px;border:1px solid #d0d0d0;background:#fff;font-size:12px;color:#777;padding:11px 15px}
.message{left:144px;top:3247px;width:911px;height:87px;border:1px solid #d0d0d0;padding:11px 15px;font-size:12px;color:#777}

/* footer */
.footer{left:0;top:3468px;width:1200px;height:99px;background:var(--footer)}
.foot-links{left:144px;top:3494px;font-size:11px;color:#ccc;display:flex;gap:9px}
.foot-copy{left:144px;top:3524px;font-size:11px;color:#bbb}
.social{right:140px;top:3504px;display:flex;gap:22px}
.social span{width:16px;height:16px;border-radius:50%;background:#8a8a8a}
</style>
</head>
<body>

<!-- background bands -->
<svg class="abs" style="left:0;top:895px" width="1200" height="1050" viewBox="0 0 1200 1050" aria-hidden="true">
  <path fill="#f6f6f7" d="M0,40 C120,0 230,0 330,45 C430,95 520,95 620,50 C720,5 820,5 920,50 C1020,95 1120,80 1200,40 V985 C1110,950 1010,950 910,990 C810,1030 700,1030 600,990 C500,950 390,950 290,990 C190,1030 90,1020 0,985 Z"/>
</svg>
<svg class="abs" style="left:0;top:2485px" width="1200" height="605" viewBox="0 0 1200 605" aria-hidden="true">
  <path fill="#f6f6f7" d="M0,50 C110,10 210,10 310,55 C410,100 510,100 610,55 C710,10 810,10 910,55 C1010,100 1110,90 1200,50 V545 C1100,510 1000,510 900,550 C800,590 700,590 600,550 C500,510 400,510 300,550 C200,590 100,580 0,545 Z"/>
</svg>

<!-- header -->
<div class="abs logo"><span>plovencast.net</span><span class="mark"></span></div>
<nav class="abs nav">
  <a class="active">Home</a><a>About Us</a><a>Services</a><a>Portfolio</a><a>News</a><a>FAQ</a><a>Contact Us</a>
</nav>

<!-- hero -->
<p class="abs hero-text">We are an Australian based Business Software Company that delivers <em>system support, security and cloud-based applications</em> for private and government clients.</p>
<div class="abs pill" style="top:387px">
  <span class="ico"><svg width="14" height="14" viewBox="0 0 24 24"><path fill="#e21b36" d="M6.6 10.8a15.1 15.1 0 0 0 6.6 6.6l2.2-2.2a1 1 0 0 1 1-.25 11.4 11.4 0 0 0 3.6.57 1 1 0 0 1 1 1V20a1 1 0 0 1-1 1A17 17 0 0 1 3 4a1 1 0 0 1 1-1h3.5a1 1 0 0 1 1 1c0 1.25.2 2.45.57 3.6a1 1 0 0 1-.25 1z"/></svg></span>
  +61 7 5550 0142
</div>
<div class="abs pill" style="top:448px">
  <span class="ico"><svg width="10" height="15" viewBox="0 0 10 15"><rect x="1" y="1" width="8" height="13" rx="1.5" fill="none" stroke="#e21b36" stroke-width="1.6"/><circle cx="5" cy="11.5" r="0.9" fill="#e21b36"/></svg></span>
  +61 0400 555 018
</div>
<div class="abs hero-art" role="img" aria-label="Illustration of an engineer at a desk managing servers, with floating code, settings and cloud icons"></div>

<!-- philosophy -->
<h2 class="abs center" style="top:688px">Our Philosophy</h2>
<p class="abs lead" style="top:742px">As system engineers, we understand that a secure and reliable back end is a vital component of every modern business and government service. This is why our team works with each client to support, protect and upgrade their systems, so their data and applications keep running.</p>
<a class="abs btn" style="left:552px;top:837px">Read More</a>

<!-- services -->
<h2 class="abs center" style="top:1056px">Services</h2>
<div class="abs card" style="left:139px;top:1135px">
  <div class="tile" style="background:var(--violet)"><svg width="50" height="46" viewBox="0 0 50 46" fill="none" stroke="#fff" stroke-width="2.4"><circle cx="25" cy="23" r="8"/><path d="M25 3v7M25 36v7M5 23h7M38 23h7M11 9l5 5M34 32l5 5M11 37l5-5M34 14l5-5"/></svg></div>
  <h3 style="color:var(--violet)">System Support</h3>
  <p>Our engineers monitor and maintain your systems around the clock, fixing issues before they slow down your staff or clients.</p>
  <a class="btn soft">Read More</a>
</div>
<div class="abs card" style="left:449px;top:1135px">
  <div class="tile" style="background:var(--indigo)"><svg width="44" height="48" viewBox="0 0 44 48" fill="none" stroke="#fff" stroke-width="2.4" stroke-linejoin="round"><path d="M22 3l17 6v13c0 11-7 19-17 23C12 41 5 33 5 22V9z"/><path d="M14 24l6 6 11-12"/></svg></div>
  <h3 style="color:var(--indigo)">Security</h3>
  <p>We harden networks, servers and applications, run regular audits and keep sensitive data protected to the standards you must meet.</p>
  <a class="btn soft">Read More</a>
</div>
<div class="abs card" style="left:759px;top:1135px">
  <div class="tile" style="background:var(--blue)"><svg width="52" height="40" viewBox="0 0 52 40" fill="none" stroke="#fff" stroke-width="2.4" stroke-linejoin="round"><path d="M14 34h26a9 9 0 0 0 0-18 13 13 0 0 0-25-3A10 10 0 0 0 14 34z"/><path d="M26 30V18M21 23l5-5 5 5"/></svg></div>
  <h3 style="color:var(--blue)">Cloud Applications</h3>
  <p>We build and migrate business applications to the cloud, so your teams can work securely from anywhere and scale as you grow.</p>
  <a class="btn soft">Read More</a>
</div>

<!-- technology -->
<h2 class="abs center" style="top:1440px">Technology</h2>
<div class="abs card" style="left:139px;top:1518px">
  <div class="tile" style="background:var(--red)"><svg width="52" height="44" viewBox="0 0 52 44" fill="none" stroke="#fff" stroke-width="2.4"><rect x="3" y="3" width="46" height="38" rx="4"/><path d="M3 13h46M20 22l-6 6 6 6M32 22l6 6-6 6M28 20l-4 16"/><circle cx="10" cy="8" r="1.2" fill="#fff"/><circle cx="16" cy="8" r="1.2" fill="#fff"/><circle cx="22" cy="8" r="1.2" fill="#fff"/></svg></div>
  <h3 style="color:var(--red)">Back-end Development</h3>
  <p>We build robust back-end systems, APIs and integrations that connect your existing tools.</p>
  <a class="btn soft">Read More</a>
</div>
<div class="abs card" style="left:449px;top:1518px">
  <div class="tile" style="background:var(--magenta)"><svg width="46" height="48" viewBox="0 0 46 48" fill="none" stroke="#fff" stroke-width="2.4"><ellipse cx="23" cy="9" rx="17" ry="6"/><path d="M6 9v30c0 3.3 7.6 6 17 6s17-2.7 17-6V9M6 19c0 3.3 7.6 6 17 6s17-2.7 17-6M6 29c0 3.3 7.6 6 17 6s17-2.7 17-6"/></svg></div>
  <h3 style="color:var(--magenta)">Data Management</h3>
  <p>We organise, back up and recover your data, so records stay accurate and always available.</p>
  <a class="btn soft">Read More</a>
</div>
<div class="abs card" style="left:759px;top:1518px">
  <div class="tile" style="background:var(--pink)"><svg width="48" height="48" viewBox="0 0 48 48" fill="none" stroke="#fff" stroke-width="2.2"><rect x="4" y="4" width="40" height="12" rx="2"/><rect x="4" y="18" width="40" height="12" rx="2"/><rect x="4" y="32" width="40" height="12" rx="2"/><circle cx="11" cy="10" r="2"/><circle cx="11" cy="24" r="2"/><circle cx="11" cy="38" r="2"/><path d="M26 10h12M26 24h12M26 38h12"/></svg></div>
  <h3 style="color:var(--pink)">Hosting Solutions</h3>
  <p>We offer secure managed hosting for all of our projects so you never have to worry about uptime, patches or finding the right home.</p>
  <a class="btn soft">Read More</a>
</div>

<!-- portfolio -->
<h2 class="abs center" style="top:1993px">Portfolio</h2>
<div class="abs shot" style="left:144px;background:linear-gradient(180deg,#3f4a5a 0 16px,#e6e9ec 16px 40%,#9fd0d8 40%,#6b8fd0 62%,#f2f2f2 62%)" role="img" aria-label="System monitoring dashboard for a government client"></div>
<div class="abs shot" style="left:452px;background:linear-gradient(180deg,#f0f0f0 0 22%,#4a63b8 22%,#9cb7e0 48%,#33408a 70%,#e9e9e9 70%)" role="img" aria-label="Cloud application interface for a private company"></div>
<div class="abs shot" style="left:759px;background:linear-gradient(180deg,#2a3552 0 4%,#3550a8 4%,#c7d6f0 45%,#f3f1ec 62%,#f6f6f6 100%)" role="img" aria-label="Security reporting portal with data charts"></div>
<a class="abs btn" style="left:552px;top:2425px">View All</a>

<!-- faq -->
<h2 class="abs center" style="top:2642px">FAQ</h2>
<p class="abs center q" style="top:2707px">How much does system support from Plovencast.net cost?</p>
<p class="abs a" style="top:2741px">There are quite a few factors that are going to affect the ultimate cost of your support plan. These factors include how many systems and users you have, whether you need cloud hosting, the level of security required, and the response times you expect.</p>
<div class="abs rule" style="top:2799px"></div>
<p class="abs center q" style="top:2826px">How long does it take to upgrade an existing system?</p>
<p class="abs a" style="top:2860px">Again it all depends on the size of your current system, how much data needs to be migrated, the integrations involved, and the security checks your sector requires. Contact us for a free assessment.</p>
<a class="abs btn" style="left:552px;top:2918px">View All</a>

<!-- contact -->
<h2 class="abs center" style="top:3133px">Contact Us</h2>
<div class="abs field" style="left:144px">Full name</div>
<div class="abs field" style="left:375px">Company name</div>
<div class="abs field" style="left:606px">Email</div>
<div class="abs field" style="left:837px">Phone</div>
<div class="abs message">Message</div>
<a class="abs btn" style="left:552px;top:3353px">Submit</a>

<!-- footer -->
<footer class="abs footer"></footer>
<div class="abs foot-links"><span>Home</span><span>|</span><span>About Us</span><span>|</span><span>Services</span><span>|</span><span>Portfolio</span><span>|</span><span>News</span><span>|</span><span>FAQ</span><span>|</span><span>Contact Us</span></div>
<div class="abs foot-copy">Copyright © 2019 Plovencast. All rights reserved.</div>
<div class="abs social"><span></span><span></span><span></span></div>

</body>
</html>
```